Professional and creative business card design for recruiting service providers

Our company supports German medium-sized companies in filling vacancies promptly. For this we use social media marketing and bring our customers into the visibility.

We want a professional but also creative design for our business cards.

Please look at lindqvar-staff.de to get an impression of our CI.

Target Market(s)

Small and medium-sized companies in Germany from the industry

Industry/Entity Type

Industrie, Handwerk

Contact Information for Business Card

Name, Position, Telefonnummer, Email, Website

Colors
EE7325
F08F49
F5BC92
FAE3D3
FDF4ED

Requirements
Must have
• A picture of the employee and in the style of www.lindqvar-staff.de

```html
<!DOCTYPE html>
<html lang="en">
<head>
<meta charset="utf-8">
<title>Lindqvar &amp; Staff – Business Card</title>
<link rel="stylesheet" href="https://fonts.googleapis.com/css2?family=Poppins:wght@700&family=Jost:wght@500&family=Arimo:wght@400&display=swap">
<style>
  :root {
    --backdrop: #b8b8b8;
    --ink: #000000;
    --paper: #ffffff;
    --accent: #ee5c2c;
    --shadow: rgba(0,0,0,0.75);
    --photo-top: #4a4038;
    --photo-bottom: #15161a;
  }
  * { margin: 0; padding: 0; box-sizing: border-box; }
  html, body { width: 1075px; height: 1200px; overflow: hidden; background: var(--backdrop); }
  .canvas { position: relative; width: 1075px; height: 1200px; }

  .card {
    position: absolute; left: 206px; width: 663px; height: 396px;
    overflow: hidden; box-shadow: 3px 3px 2px var(--shadow);
  }
  .card--front { top: 187px; background: var(--paper); }
  .card--back { top: 637px; background: var(--ink); }

  .brand { position: absolute; display: flex; align-items: center; }
  .brand__mark { background: var(--accent); flex: none; }
  .brand__name {
    font-family: "Poppins", sans-serif; font-weight: 700;
    letter-spacing: 2px; line-height: 1.02; text-transform: uppercase;
  }
  .card--front .brand { left: 35px; top: 88px; gap: 18px; }
  .card--front .brand__mark { width: 64px; height: 64px; }
  .card--front .brand__name { font-size: 31px; color: var(--ink); }

  .card--back .brand { left: 50%; top: 197px; transform: translate(-50%, -50%); gap: 24px; }
  .card--back .brand__mark { width: 84px; height: 84px; }
  .card--back .brand__name { font-size: 40px; color: var(--paper); }

  .person { position: absolute; left: 35px; top: 216px; }
  .person__name {
    font-family: "Jost", sans-serif; font-weight: 500; font-size: 30px;
    color: var(--accent); line-height: 1; text-transform: uppercase;
  }
  .person__role {
    font-family: "Arimo", sans-serif; font-size: 17px; line-height: 1; color: var(--ink);
    margin-top: 3px; text-transform: uppercase;
  }
  .person-rule { position: absolute; left: 0; top: 276px; width: 259px; height: 3px; background: var(--accent); }

  .portrait {
    position: absolute; left: 347px; top: 29px; width: 280px; height: 250px;
    background: linear-gradient(180deg, var(--photo-top) 0%, var(--photo-bottom) 70%);
    border-radius: 120px 120px 0 0;
  }

  .contact-band { position: absolute; left: 0; top: 279px; width: 100%; height: 117px; background: var(--ink); }
  .contact-list { position: absolute; left: 35px; top: 22px; list-style: none; }
  .contact-list li {
    display: flex; align-items: center; gap: 6px; height: 24px;
    font-family: "Arimo", sans-serif; font-size: 17.5px; color: var(--paper);
  }
  .contact-list svg { width: 17px; height: 17px; flex: none; }

  .web-band {
    position: absolute; left: 0; bottom: 0; width: 100%; height: 45px;
    background: var(--accent); display: flex; align-items: center; justify-content: center;
    font-family: "Arimo", sans-serif; font-size: 17.5px; color: var(--paper);
  }
</style>
</head>
<body>
<main class="canvas">
  <section class="card card--front">
    <div class="brand">
      <span class="brand__mark"></span>
      <span class="brand__name">Lindqvar<br>&amp; Staff</span>
    </div>

    <div class="portrait" role="img" aria-label="Portrait photo of the employee in a dark blazer and turtleneck"></div>

    <div class="person">
      <p class="person__name">Lukas Brenner</p>
      <p class="person__role">Managing Director</p>
    </div>
    <div class="person-rule"></div>

    <div class="contact-band">
      <ul class="contact-list">
        <li>
          <svg viewBox="0 0 24 24" aria-hidden="true"><path fill="#ee5c2c" d="M6.6 10.8a15 15 0 0 0 6.6 6.6l2.2-2.2a1 1 0 0 1 1-.25 11.4 11.4 0 0 0 3.6.57 1 1 0 0 1 1 1V20a1 1 0 0 1-1 1A17 17 0 0 1 3 4a1 1 0 0 1 1-1h3.5a1 1 0 0 1 1 1c0 1.25.2 2.45.57 3.57a1 1 0 0 1-.25 1z"/><path fill="none" stroke="#ee5c2c" stroke-width="1.8" d="M14 3a7 7 0 0 1 7 7M14 7a3 3 0 0 1 3 3"/></svg>
          049-870 312 645
        </li>
        <li>
          <svg viewBox="0 0 24 24" aria-hidden="true"><rect x="2" y="5" width="20" height="14" fill="#ee5c2c"/><path d="M2 5l10 8 10-8M2 19l8-7M22 19l-8-7" fill="none" stroke="#000" stroke-width="1.5"/></svg>
          info@lindqvar-staff.de
        </li>
        <li>
          <svg viewBox="0 0 24 24" aria-hidden="true"><g fill="none" stroke="#ee5c2c" stroke-width="1.8"><circle cx="12" cy="12" r="9.5"/><ellipse cx="12" cy="12" rx="4" ry="9.5"/><path d="M2.5 12h19M4 7h16M4 17h16"/></g></svg>
          www.lindqvar-staff.de
        </li>
      </ul>
    </div>
  </section>

  <section class="card card--back">
    <div class="brand">
      <span class="brand__mark"></span>
      <span class="brand__name">Lindqvar<br>&amp; Staff</span>
    </div>
    <div class="web-band">www.lindqvar-staff.de</div>
  </section>
</main>
</body>
</html>
```